Folded A4 flyer for design&construction company

Folded A4 flyer needed. Keywords: elegant, stylish
our website www.dorvika.ae

Industry/Entity Type

Construction

```html
<!DOCTYPE html>
<html lang="en">
<head>
<meta charset="UTF-8">
<title>Dorvika – Design &amp; Construction Brochure Cover</title>
<link rel="stylesheet" href="https://fonts.googleapis.com/css2?family=Open+Sans:wght@400;700&family=Courgette&display=swap">
<style>
  :root {
    --backdrop: #bab9b5;
    --cover-grey: #5c5d62;
    --cover-grey-dark: #4f5055;
    --gold: #c9a227;
    --gold-light: #e2c45a;
    --white: #ffffff;
    --wood: #c98f2a;
    --ochre: #e7a61c;
    --wall: #f1efe9;
  }
  * { margin: 0; padding: 0; box-sizing: border-box; }
  html, body {
    width: 1200px;
    height: 789px;
    overflow: hidden;
    background: var(--backdrop);
  }
  .canvas {
    position: relative;
    width: 1200px;
    height: 789px;
  }
  .brochure-cover {
    position: absolute;
    left: 338px;
    top: 24px;
    width: 524px;
    height: 740px;
    background: var(--cover-grey);
    box-shadow: 0 6px 18px rgba(0,0,0,0.25);
    overflow: hidden;
  }
  .cover-header {
    position: absolute;
    top: 0; left: 0; right: 0;
    height: 215px;
    display: flex;
    flex-direction: column;
    align-items: center;
    justify-content: flex-end;
    padding-bottom: 24px;
  }
  .brand-name {
    font-family: "Open Sans", sans-serif;
    font-weight: 400;
    font-size: 74px;
    letter-spacing: 2px;
    line-height: 1;
    color: var(--white);
  }
  .brand-tagline {
    margin-top: 6px;
    font-family: "Courgette", cursive;
    font-size: 19px;
    color: var(--gold);
    letter-spacing: 0.5px;
  }
  .cover-photo {
    position: absolute;
    top: 215px; left: 0; right: 0;
    height: 365px;
    background:
      radial-gradient(ellipse 60% 30% at 60% 18%, var(--wall) 0%, rgba(241,239,233,0) 70%),
      linear-gradient(180deg, var(--ochre) 0%, #f2d68c 30%, var(--wall) 48%, #d9a653 62%, var(--wood) 100%);
  }
  .cover-quote {
    position: absolute;
    left: 40px;
    right: 30px;
    top: 540px;
    font-family: "Courgette", cursive;
    font-size: 21px;
    color: var(--white);
    text-align: center;
    text-shadow: 0 1px 3px rgba(0,0,0,0.35);
  }
  .cover-footer {
    position: absolute;
    top: 580px; left: 0; right: 0; bottom: 0;
    background: var(--cover-grey);
  }
  .web-bar {
    position: absolute;
    left: 36px;
    right: 36px;
    top: 78px;
    height: 44px;
    background: linear-gradient(90deg, rgba(201,162,39,0) 0%, var(--gold) 30%, var(--gold-light) 55%, var(--gold) 78%, rgba(201,162,39,0) 100%);
    display: flex;
    align-items: center;
    justify-content: center;
  }
  .web-address {
    font-family: "Open Sans", sans-serif;
    font-weight: 700;
    font-size: 20px;
    letter-spacing: 1px;
    color: var(--white);
    text-transform: uppercase;
  }
</style>
</head>
<body>
  <div class="canvas">
    <article class="brochure-cover">
      <header class="cover-header">
        <div class="brand-name">DORVIKA</div>
        <div class="brand-tagline">design &amp; construction</div>
      </header>

      <div class="cover-photo" role="img" aria-label="Bright modern interior with a curved white staircase, ochre ceiling curves, black lounge chairs and a glossy wooden floor"></div>

      <p class="cover-quote">Quality is not an act, it is a habit - Theron Vale</p>

      <footer class="cover-footer">
        <div class="web-bar">
          <span class="web-address">www.dorvika.ae</span>
        </div>
      </footer>
    </article>
  </div>
</body>
</html>
```